Redesign of business card for Cedar Ridge Mechanical

We are looking for a new design for our business cards for Cedar Ridge Mechanical. We are a plumbing & HVAC construction company, operating on the West Coast of Canada and USA. Logo attached.
Industry/Entity Type
Construction - Plumbing & HVAC
Contact Information for Business Card
Name, address, phone numbers, email, website address
Look and feel
Each slider illustrates characteristics of the customer's brand and the style your logo design should communicate.

```html
<!DOCTYPE html>
<html lang="en">
<head>
<meta charset="utf-8">
<title>Cedar Ridge Mechanical – Business Card</title>
<link href="https://fonts.googleapis.com/css2?family=Lato:wght@400&family=Montserrat:wght@400;700&display=swap" rel="stylesheet">
<style>
  :root {
    --backdrop: #9a9a9a;
    --card-front: #ffffff;
    --card-back: #1a1a1a;
    --ink: #111111;
    --ink-soft: #2b2b2b;
    --brand: #333333;
    --brand-faint: #3d3d3d;
  }
  * { margin: 0; padding: 0; box-sizing: border-box; }
  html, body { width: 1200px; height: 1059px; overflow: hidden; }
  body { background: var(--backdrop); position: relative; font-family: "Lato", sans-serif; }

  .card { position: absolute; left: 253px; width: 707px; height: 404px; }
  .card--front { top: 86px; background: var(--card-front); }
  .card--back { top: 563px; background: var(--card-back); }

  .brand-lockup {
    position: absolute; display: flex; align-items: center;
    font-family: "Montserrat", sans-serif; font-weight: 700; text-transform: uppercase;
  }
  .card--front .brand-lockup {
    left: 96px; top: 152px; width: 210px; gap: 12px; color: var(--brand);
    font-size: 19px; line-height: 1.15; letter-spacing: 0.5px;
  }
  .brand-mark { flex: none; width: 30px; height: 30px; background: currentColor; }
  .card--back .brand-lockup {
    left: 0; right: 0; top: 150px; justify-content: center; gap: 20px;
    color: var(--brand-faint); font-size: 34px; letter-spacing: 1px;
  }
  .card--back .brand-mark { width: 48px; height: 48px; }

  .divider { position: absolute; left: 346px; top: 97px; width: 2px; height: 213px; background: var(--ink-soft); }

  .person-name {
    position: absolute; left: 380px; top: 92px;
    font-family: "Montserrat", sans-serif; font-weight: 700; font-size: 25px; color: var(--ink);
  }
  .person-title {
    position: absolute; left: 379px; top: 131px;
    font-family: "Montserrat", sans-serif; font-weight: 400; font-size: 18px; color: var(--ink-soft);
  }
  .contact-list { position: absolute; left: 375px; top: 177px; list-style: none; }
  .contact-item { display: flex; align-items: center; height: 25px; font-size: 18px; color: var(--ink); }
  .contact-item svg { width: 18px; height: 18px; margin-right: 14px; fill: var(--ink); }
  .address { position: absolute; left: 371px; top: 261px; font-size: 18px; line-height: 24px; color: var(--ink); }
</style>
</head>
<body>
  <section class="card card--front">
    <div class="brand-lockup">
      <span class="brand-mark"></span>
      <span class="brand-name">Cedar Ridge Mechanical</span>
    </div>
    <div class="divider"></div>
    <h1 class="person-name">DANIEL HAYES</h1>
    <p class="person-title">MANAGING DIRECTOR</p>
    <ul class="contact-list">
      <li class="contact-item">
        <svg viewBox="0 0 24 24" aria-hidden="true"><path d="M6.6 10.8a15.1 15.1 0 0 0 6.6 6.6l2.2-2.2c.3-.3.7-.4 1-.2 1.1.4 2.3.6 3.6.6.6 0 1 .4 1 1V20c0 .6-.4 1-1 1C10.6 21 3 13.4 3 4c0-.6.4-1 1-1h3.5c.6 0 1 .4 1 1 0 1.3.2 2.5.6 3.6.1.3 0 .7-.2 1z"/></svg>
        044-123 456 789
      </li>
      <li class="contact-item">
        <svg viewBox="0 0 24 24" aria-hidden="true"><path d="M2 5h20v14H2z M3.5 6.5 12 12.5l8.5-6" fill="none" stroke="#111" stroke-width="0"/><path d="M2 5h20v2l-10 6L2 7z"/><path d="M2 9l10 6 10-6v10H2z"/></svg>
        info@webname.com
      </li>
      <li class="contact-item">
        <svg viewBox="0 0 24 24" aria-hidden="true"><path d="M12 2a10 10 0 1 0 0 20 10 10 0 0 0 0-20zm0 2a8 8 0 0 1 6.9 4H16l-2 2 1 3-2 2v3l-2 1v-4l-3-2V9l-3-1A8 8 0 0 1 12 4z"/></svg>
        www.websitename.com
      </li>
    </ul>
    <p class="address">421, Address line goes here<br>45452, Country name</p>
  </section>

  <section class="card card--back">
    <div class="brand-lockup">
      <span class="brand-mark"></span>
      <span class="brand-name">Cedar Ridge Mechanical</span>
    </div>
  </section>
</body>
</html>
```